Redesign Craft Brewing Recipe Website

Originally built with Bootstrap just to get the site going, I am seeking a complete redesign of the sites home page and recipe page. I am an experienced web developer with no graphic background, initially just looking for psd mocks.

I prefer styles that are clean and modern, and would prefer anything that is fun, engaging, and has an organic feel to it. I currently have a cartoon rabbit as a logo, but it needs some modification/tweaking, so any help in that area would be great as well.

Current site:
http://velvetfinch.cloudpagehost.net/

Current launch page/logo:
http://www.velvetfinch.com/

I like the overall layout of the elements currently, but the design sucks.

The launch page is at the following URL

Reason: Still looking for a more modern design. Designs received so far are too similar to the original.

My site is content based and does not contain images or products. Your design should not consist of large images.

Reason: The website has very little images, so the designs need to be more text and content based. The header needs to be very small and should not contain an ad rotater.

Target Market(s)

Home brewers, Craft brewers, Microbreweries, Brewpubs

Requirements
Must have
• Web 2.0 Look and Feel, Fun, Hip, Focus on content
Should not have
• A large photo as a header

```html
<!DOCTYPE html>
<html lang="en">
<head>
<meta charset="utf-8">
<title>Velvetfinch – Latest Recipes</title>
<link href="https://fonts.googleapis.com/css2?family=Roboto+Condensed:wght@400;700&family=Roboto:wght@400;500&family=Roboto+Mono&display=swap" rel="stylesheet">
<style>
:root{
  --maroon:#5c0a1c;
  --crimson:#a3163a;
  --gold:#e0b35c;
  --page:#edebe6;
  --panel:#fbfbfa;
  --line:#dedbd6;
  --ink:#333;
  --muted:#999;
  --mocha:#8c6b62;
  --leaf:#2f5a0a;
  --slate:#4e5a67;
  --clay:#a07a6e;
  --charcoal:#353a36;
  --bar:#3b3b3b;
}
*{box-sizing:border-box;margin:0;padding:0}
html,body{width:1173px;height:1200px;overflow:hidden;background:var(--page)}
body{font-family:"Roboto",Arial,sans-serif;color:var(--ink)}
.stage{position:relative;width:1200px;height:1228px;transform:scale(.9775);transform-origin:0 0}
.site-header{position:absolute;left:0;top:0;width:1200px;height:118px;background:var(--maroon)}
.brand{position:absolute;left:125px;top:26px;display:flex;align-items:flex-start;gap:14px}
.brand-mark{width:60px;height:60px;border-radius:50%;background:var(--gold);margin-top:6px}
.brand-name{font-family:"Roboto Condensed",sans-serif;font-weight:700;font-size:42px;line-height:44px;color:var(--gold)}
.brand-tag{font-size:12.5px;line-height:14px;color:#c79a86;margin-top:2px}
.main-nav{position:absolute;right:110px;top:0;display:flex;gap:0}
.main-nav a{display:block;height:118px;padding:54px 19px 0;font-family:"Roboto Condensed",sans-serif;font-size:15px;color:var(--gold);text-decoration:none;position:relative}
.main-nav a.active::after{content:"";position:absolute;left:0;right:0;bottom:0;height:5px;background:var(--crimson)}
.sidebar{position:absolute;left:110px;top:146px;width:237px;height:1017px;background:var(--panel);border:1px solid var(--line)}
.side-h{position:absolute;font-family:"Roboto Condensed",sans-serif;font-size:21px;color:#4a4f55}
.side-h span{color:var(--mocha)}
.field{position:absolute;left:13px;width:211px;height:31px;background:#fff;border:1px solid var(--line);font-size:14px;color:#555;padding:7px 0 0 21px}
.field.placeholder{color:#aaa}
.field .radio{position:absolute;right:18px;top:10px;width:9px;height:9px;border:1px solid #bbb;border-radius:50%}
.field .radio::after{content:"";position:absolute;left:2px;top:2px;width:3px;height:3px;border-radius:50%;background:#333}
.field .caret{position:absolute;right:18px;top:13px;border:4px solid transparent;border-top:5px solid #555}
.range-label{position:absolute;left:16px;top:386px;font-size:12px;color:#444}
.range{position:absolute;left:13px;top:413px;width:210px}
.range .track{height:8px;border:1px solid #ccc;border-radius:4px;background:#f2f2f2;position:relative}
.range .fill{position:absolute;left:56px;right:22px;top:0;bottom:0;background:#b89c94}
.range .knob{position:absolute;top:-5px;width:14px;height:16px;background:#fafafa;border:1px solid #aaa;border-radius:3px}
.range .ticks{display:flex;justify-content:space-between;font-size:9px;color:#444;margin-top:12px;padding:0 2px}
.update-btn{position:absolute;left:7px;top:472px;width:222px;height:34px;background:var(--bar);border:1px solid #222;border-radius:2px;color:#fff;font-family:"Roboto Condensed",sans-serif;font-size:14px;text-align:center;line-height:32px}
.content{position:absolute;left:359px;top:146px;width:733px;height:1017px;background:#fff;border:1px solid var(--line)}
.content-title{position:absolute;left:17px;top:18px;font-family:"Roboto Condensed",sans-serif;font-size:43px;color:var(--ink);letter-spacing:-.5px}
.content-title span{color:var(--mocha)}
.sort{position:absolute;right:13px;top:35px;font-size:15px;color:#333}
.sort .on{color:var(--crimson)}.sort .off{color:var(--mocha)}
.grid{position:absolute;left:0;top:84px;width:732px;display:grid;grid-template-columns:366px 366px;grid-template-rows:220px 220px 219px 219px;border-top:1px solid var(--line)}
.recipe{position:relative;border-bottom:1px solid var(--line)}
.recipe:nth-child(odd){border-right:1px solid var(--line)}
.thumb{position:absolute;left:12px;top:26px;width:94px;height:97px;border:1px solid var(--line);background:linear-gradient(90deg,#f4f4f4,#e6e6e6)}
.thumb i{display:block;position:absolute;left:7px;right:7px;top:8px;bottom:6px;background:linear-gradient(90deg,#6f7a24 0 30%,transparent 30% 35%,#b02a30 35% 65%,transparent 65% 70%,#1f1f22 70%)}
.tag{position:absolute;left:12px;width:94px;height:32px;font-family:"Roboto Condensed",sans-serif;font-size:16px;color:#fff;text-align:center;line-height:32px}
.tag.extract{top:130px;background:var(--crimson)}
.tag.style{top:166px;background:var(--charcoal)}
.tag.style.flag{border-top:4px solid var(--crimson);line-height:28px}
.recipe h3{position:absolute;left:115px;top:28px;width:180px;font-family:"Roboto Condensed",sans-serif;font-weight:400;font-size:19px;line-height:18px;color:var(--leaf)}
.byline{position:absolute;left:116px;top:71px;font-size:12px;color:var(--muted)}
.byline b{font-family:"Roboto Condensed",sans-serif;font-weight:400;color:#333}
.blurb{position:absolute;left:116px;top:94px;width:188px;font-size:12.5px;line-height:18px;color:#999}
.stats{position:absolute;left:308px;top:8px;width:48px;height:200px;background:var(--slate);color:#fff;font-size:10px;line-height:11px;text-align:center;font-weight:500}
.stats div{height:39.5px;padding-top:9px}
.stats .srm{background:var(--clay);height:42px;margin-top:2px}
.results-bar{position:absolute;left:359px;top:1108px;width:733px;height:55px;background:var(--bar);border-radius:0 0 3px 3px;color:#fff;font-family:"Roboto Condensed",sans-serif;font-size:15px}
.results-bar .cell{position:absolute;top:0;height:55px;line-height:55px;border-right:1px solid #222}
.pager{position:absolute;right:10px;top:16px;display:flex;gap:6px}
.pager span{display:block;height:24px;padding:0 11px;background:#fff;border:1px solid #ccc;border-radius:2px;color:#333;font-family:"Roboto",sans-serif;font-size:12px;line-height:22px}
.copyright{position:absolute;right:110px;top:1188px;font-family:"Roboto Condensed",sans-serif;font-size:13px;color:#333}
</style>
</head>
<body>
<div class="stage">
  <header class="site-header">
    <div class="brand">
      <div class="brand-mark"></div>
      <div>
        <div class="brand-name">Velvetfinch</div>
        <div class="brand-tag">Easiest way to create and share<br>craft beer recipes.</div>
      </div>
    </div>
    <nav class="main-nav">
      <a class="active" href="#">HOME</a><a href="#">RECIPES</a><a href="#">ABOUT US</a><a href="#">OUR CLIENTS</a><a href="#">CONTACT</a>
    </nav>
  </header>

  <aside class="sidebar">
    <div class="side-h" style="left:19px;top:36px">Search <span>Recipes</span></div>
    <div class="field placeholder" style="top:73px">Stout</div>
    <div class="side-h" style="left:20px;top:126px">Match Maker</div>
    <div class="field" style="top:159px">Boil Size<span class="radio"></span></div>
    <div class="side-h" style="left:18px;top:213px">Brewing</div>
    <div class="field" style="top:248px;font-size:12.5px">Extract<span class="caret"></span></div>
    <div class="side-h" style="left:17px;top:303px">Styles</div>
    <div class="field" style="top:335px;font-size:13px">American Amber Ale<span class="caret"></span></div>
    <div class="range-label">0 Gals to 25 Gals</div>
    <div class="range">
      <div class="track"><div class="fill"></div><span class="knob" style="left:49px"></span><span class="knob" style="left:180px"></span></div>
      <div class="ticks"><span>0</span><span>5</span><span>10</span><span>15</span><span>20</span><span>25</span></div>
    </div>
    <div class="update-btn">UPDATE SEARCH</div>
  </aside>

  <main class="content">
    <h1 class="content-title">Latest <span>Recipes</span></h1>
    <div class="sort"><span class="on">Popular</span> &nbsp;/&nbsp; <span class="off">Recent</span></div>
    <div class="grid">
      <!-- recipe cards -->
      <article class="recipe"><div class="thumb" role="img" aria-label="Three wine bottles: green, red and black"><i></i></div><div class="tag extract">Extract</div><div class="tag style">Sweet Mead</div><h3>Oak Hollow Sweet Mead</h3><p class="byline">Created by <b>Harold Pine</b></p><p class="blurb">Le Lorem Ipsum est simplement du faux texte employé dans la composition mise en page avant impression. Lorem Ipsum est le faux texte merie depuis les années 1500.</p><div class="stats"><div>2.24%<br>abv</div><div>24<br>ibu</div><div>1.006<br>fb</div><div>1.022<br>og</div><div class="srm">9<br>SRM</div></div></article>
      <article class="recipe"><div class="thumb" role="img" aria-label="Three wine bottles: green, red and black"><i></i></div><div class="tag extract">Extract</div><div class="tag style">Sweet Mead</div><h3>Oak Hollow Sweet Mead</h3><p class="byline">Created by <b>Harold Pine</b></p><p class="blurb">Le Lorem Ipsum est simplement du faux texte employé dans la composition mise en page avant impression. Lorem Ipsum est le faux texte merie depuis les années 1500.</p><div class="stats"><div>2.24%<br>abv</div><div>24<br>ibu</div><div>1.006<br>fb</div><div>1.022<br>og</div><div class="srm">9<br>SRM</div></div></article>
      <article class="recipe"><div class="thumb" role="img" aria-label="Three wine bottles: green, red and black"><i></i></div><div class="tag extract">Extract</div><div class="tag style">Sweet Mead</div><h3>Oak Hollow Sweet Mead</h3><p class="byline">Created by <b>Harold Pine</b></p><p class="blurb">Le Lorem Ipsum est simplement du faux texte employé dans la composition mise en page avant impression. Lorem Ipsum est le faux texte merie depuis les années 1500.</p><div class="stats"><div>2.24%<br>abv</div><div>24<br>ibu</div><div>1.006<br>fb</div><div>1.022<br>og</div><div class="srm">9<br>SRM</div></div></article>
      <article class="recipe"><div class="thumb" role="img" aria-label="Three wine bottles: green, red and black"><i></i></div><div class="tag style flag">Sweet Mead</div><h3>Oak Hollow Sweet Mead</h3><p class="byline">Created by <b>Harold Pine</b></p><p class="blurb">Le Lorem Ipsum est simplement du faux texte employé dans la composition mise en page avant impression. Lorem Ipsum est le faux texte merie depuis les années 1500.</p><div class="stats"><div>2.24%<br>abv</div><div>24<br>ibu</div><div>1.006<br>fb</div><div>1.022<br>og</div><div class="srm">9<br>SRM</div></div></article>
      <article class="recipe"><div class="thumb" role="img" aria-label="Three wine bottles: green, red and black"><i></i></div><div class="tag extract">Extract</div><div class="tag style">Sweet Mead</div><h3>Oak Hollow Sweet Mead</h3><p class="byline">Created by <b>Harold Pine</b></p><p class="blurb">Le Lorem Ipsum est simplement du faux texte employé dans la composition mise en page avant impression. Lorem Ipsum est le faux texte merie depuis les années 1500.</p><div class="stats"><div>2.24%<br>abv</div><div>24<br>ibu</div><div>1.006<br>fb</div><div>1.022<br>og</div><div class="srm">9<br>SRM</div></div></article>
      <article class="recipe"><div class="thumb" role="img" aria-label="Three wine bottles: green, red and black"><i></i></div><div class="tag extract">Extract</div><div class="tag style">Sweet Mead</div><h3>Oak Hollow Sweet Mead</h3><p class="byline">Created by <b>Harold Pine</b></p><p class="blurb">Le Lorem Ipsum est simplement du faux texte employé dans la composition mise en page avant impression. Lorem Ipsum est le faux texte merie depuis les années 1500.</p><div class="stats"><div>2.24%<br>abv</div><div>24<br>ibu</div><div>1.006<br>fb</div><div>1.022<br>og</div><div class="srm">9<br>SRM</div></div></article>
      <article class="recipe"><div class="thumb" role="img" aria-label="Three wine bottles: green, red and black"><i></i></div><div class="tag extract">Extract</div><div class="tag style">Sweet Mead</div><h3>Oak Hollow Sweet Mead</h3><p class="byline">Created by <b>Harold Pine</b></p><p class="blurb">Le Lorem Ipsum est simplement du faux texte employé dans la composition mise en page avant impression. Lorem Ipsum est le faux texte merie depuis les années 1500.</p><div class="stats"><div>2.24%<br>abv</div><div>24<br>ibu</div><div>1.006<br>fb</div><div>1.022<br>og</div><div class="srm">9<br>SRM</div></div></article>
      <article class="recipe"><div class="thumb" role="img" aria-label="Three wine bottles: green, red and black"><i></i></div><div class="tag extract">Extract</div><div class="tag style">Sweet Mead</div><h3>Oak Hollow Sweet Mead</h3><p class="byline">Created by <b>Harold Pine</b></p><p class="blurb">Le Lorem Ipsum est simplement du faux texte employé dans la composition mise en page avant impression. Lorem Ipsum est le faux texte merie depuis les années 1500.</p><div class="stats"><div>2.24%<br>abv</div><div>24<br>ibu</div><div>1.006<br>fb</div><div>1.022<br>og</div><div class="srm">9<br>SRM</div></div></article>
    </div>
  </main>

  <div class="results-bar">
    <div class="cell" style="left:0;width:125px;padding-left:19px">Search Result</div>
    <div class="cell" style="left:125px;width:99px;padding-left:21px">12 Found</div>
    <div class="pager"><span>Prev</span><span>Next</span></div>
  </div>

  <footer class="copyright">Copyright 2013 Website Name. All Rights Reserved.</footer>
</div>
</body>
</html>
```